Business card design for Calderin Engineering Tandem

We need a new business card design along with all the necessary to place an order. The company is Calderin Engineering Tandem and we recently updated our logo.

```html
<!DOCTYPE html>
<html lang="en">
<head>
<meta charset="utf-8">
<title>Calderin Engineering Tandem — Business Card</title>
<link rel="stylesheet" href="https://fonts.googleapis.com/css2?family=Jost:wght@400;500;700&display=swap">
<style>
  :root {
    --backdrop: #3a3a3a;
    --card: #262626;
    --card-edge: #1c1c1c;
    --grey: #a3a3a3;
    --grey-light: #c4c4c4;
    --yellow: #eac42a;
    --divider: #6b6b6b;
  }
  * { box-sizing: border-box; margin: 0; padding: 0; }
  html, body {
    width: 1200px; height: 982px; overflow: hidden;
    background: var(--backdrop);
    font-family: "Jost", sans-serif;
  }
  .stage {
    position: relative; width: 1200px; height: 982px;
    display: flex; flex-direction: column; align-items: center; justify-content: center; gap: 56px;
  }
  .card {
    position: relative; width: 700px; height: 400px;
    background: var(--card);
    border-radius: 26px;
    box-shadow: 0 14px 30px rgba(0,0,0,.45);
    border: 1px solid var(--card-edge);
  }
  /* Front */
  .card--front { display: flex; align-items: center; justify-content: center; }
  .brand {
    display: flex; align-items: center; gap: 14px;
    color: var(--grey); font-weight: 500; letter-spacing: 1px;
    white-space: nowrap;
  }
  .brand__mark { width: 14px; height: 14px; background: var(--yellow); flex: none; }
  .brand--large { font-size: 38px; }
  /* Back */
  .card--back { display: flex; align-items: center; }
  .back__brand-area { width: 340px; padding: 0 24px; display: flex; justify-content: center; }
  .brand--small { font-size: 19px; gap: 10px; letter-spacing: .5px; }
  .brand--small .brand__mark { width: 10px; height: 10px; }
  .divider { width: 1px; height: 290px; background: var(--divider); flex: none; }
  .contact { padding-left: 34px; }
  .contact__name {
    color: var(--grey-light); font-weight: 700; font-size: 30px; letter-spacing: .5px; line-height: 1;
  }
  .contact__title { color: var(--yellow); font-size: 18px; margin: 6px 0 16px; }
  .contact__list { list-style: none; }
  .contact__item {
    display: flex; align-items: flex-start; gap: 12px;
    color: var(--grey); font-size: 16px; line-height: 1.35; margin-bottom: 6px;
  }
  .contact__item svg { width: 15px; height: 15px; flex: none; margin-top: 3px; fill: var(--yellow); }
</style>
</head>
<body>
<main class="stage">
  <section class="card card--front" aria-label="Card front">
    <div class="brand brand--large">
      <span class="brand__mark"></span>
      <span class="brand__name">Calderin Engineering Tandem</span>
    </div>
  </section>

  <section class="card card--back" aria-label="Card back">
    <div class="back__brand-area">
      <div class="brand brand--small">
        <span class="brand__mark"></span>
        <span class="brand__name">Calderin Engineering Tandem</span>
      </div>
    </div>
    <div class="divider"></div>
    <div class="contact">
      <h1 class="contact__name">DANIEL REYES</h1>
      <p class="contact__title">Founder &amp; CEO</p>
      <ul class="contact__list">
        <li class="contact__item">
          <svg viewBox="0 0 16 16"><path d="M8 0a5.5 5.5 0 0 0-5.5 5.5C2.5 10 8 16 8 16s5.5-6 5.5-10.5A5.5 5.5 0 0 0 8 0zm0 7.7a2.2 2.2 0 1 1 0-4.4 2.2 2.2 0 0 1 0 4.4z"/></svg>
          <span>423 Street Address Here, City<br>State, Country, ZIP Code</span>
        </li>
        <li class="contact__item">
          <svg viewBox="0 0 16 16"><path d="M3.6 1 6 3.8 4.6 5.6a9 9 0 0 0 5.8 5.8L12.2 10 15 12.4l-1.6 2.4C6.8 14.6 1.4 9.2 1.2 2.6z"/></svg>
          <span>(123) 456-7890</span>
        </li>
        <li class="contact__item">
          <svg viewBox="0 0 16 16"><path d="M4.5 0h7A1.5 1.5 0 0 1 13 1.5v13a1.5 1.5 0 0 1-1.5 1.5h-7A1.5 1.5 0 0 1 3 14.5v-13A1.5 1.5 0 0 1 4.5 0zM5 2v10h6V2zm3 11a1 1 0 1 0 0 2 1 1 0 0 0 0-2z"/></svg>
          <span>(123) 456-7890</span>
        </li>
        <li class="contact__item">
          <svg viewBox="0 0 16 16"><path d="M4 0h8v4H4zM1 5h14v7h-3v4H4v-4H1zm4 5v4h6v-4z"/></svg>
          <span>(123) 456-7890</span>
        </li>
        <li class="contact__item">
          <svg viewBox="0 0 16 16"><path d="M0 3h16v1.2L8 9 0 4.2zm0 2.6 8 4.8 8-4.8V13H0z"/></svg>
          <span>info@yourwebsitehere.com</span>
        </li>
        <li class="contact__item">
          <svg viewBox="0 0 16 16"><path d="M8 0a8 8 0 1 0 0 16A8 8 0 0 0 8 0zm0 1.5c.9 0 2 1.9 2.3 4.8H5.7C6 3.4 7.1 1.5 8 1.5zM5.7 7.8h4.6C10 10.6 8.9 14.5 8 14.5S6 10.6 5.7 7.8zM1.6 7.8h2.6c.1 2 .5 3.8 1.2 5.2a6.5 6.5 0 0 1-3.8-5.2zm0-1.5a6.5 6.5 0 0 1 3.8-5.2c-.7 1.4-1.1 3.2-1.2 5.2zm10.2 1.5h2.6a6.5 6.5 0 0 1-3.8 5.2c.7-1.4 1.1-3.2 1.2-5.2zm0-1.5c-.1-2-.5-3.8-1.2-5.2a6.5 6.5 0 0 1 3.8 5.2z"/></svg>
          <span>yourwebsitehere.com</span>
        </li>
      </ul>
    </div>
  </section>
</main>
</body>
</html>
```